Talon Microsystems PowerPoint Master Slide Deck Design

This is a 2-phase project to design a slide deck for a semiconductor company in the Silicon Valley. The design budget will be increased with each phase.
The slide deck will need to have one version with a dark background for presentations and a second version with a white background. Otherwise, the slides will be the same. I anticipate we will need a total of 10 slides, but that number may change.
The first phase will be to design a Title and a Title and Content slide.
- The Title Slide is the first slide of the deck. It should include the presentation title, the presenter's name and date of presentation
- The Title and Content slide should include a title and content with bullet points and up to 2 additional sub-bullets
- The Title and Content slide should have a footer that includes the slide #, Talon Microsystems Confidential, and the logo. This footer will be on every slide except the Title Slide
The first two slides will serve as the format for the remaining ~8 slides:
-Header and Content Text (1, 2, 4 column)
-Header and Content Image (bar chart, pie chart, tables)
-Break
-Title only
-Closing (Talon logo only)
Our slides contain a lot of content so a clean and simple design is best.
Both phases will need to include pre-set color options for
-Text and Lines
-Shadows
-Bullets and sub-bullets (including shapes, ex. circle, slash, square, etc.)
-Bar charts, pie charts, tables
Samples of our collateral are attached. Logo files are also attached
Look and feel
Each slider illustrates characteristics of the customer's brand and the style your logo design should communicate.

```html
<!DOCTYPE html>
<html lang="en">
<head>
<meta charset="utf-8">
<title>Talon Microsystems Slide Master</title>
<link href="https://fonts.googleapis.com/css2?family=Roboto:wght@400;500;700;900&display=swap" rel="stylesheet">
<style>
:root{
  --board:#8f8f8f;
  --blue:#0a22f0;
  --sky:#00a8ff;
  --navy:#02051f;
  --ink:#2b2b2b;
  --paper:#ffffff;
}
*{box-sizing:border-box;margin:0;padding:0}
html,body{width:1200px;height:2222px;overflow:hidden;background:var(--board);font-family:'Roboto',Arial,sans-serif}
.slide{
  --bg:var(--paper);--fg:var(--ink);--muted:#444;--grid:#e3e6ee;--plot:transparent;
  position:absolute;width:464px;height:261px;overflow:hidden;background:var(--bg);color:var(--fg)
}
.slide.dark{--bg:var(--navy);--fg:#ffffff;--muted:#e6e8f2;--grid:#1b2045;--plot:#0a0f30}
.col-l{left:88px}.col-r{left:644px}
.r1{top:89px}.r2{top:386px}.r3{top:683px}.r4{top:980px}.r5{top:1278px}.r6{top:1575px}.r7{top:1872px}

/* cover */
.cover-art{position:absolute;inset:0;background:linear-gradient(115deg,#0b2cf2 0%,#1a5cf6 50%,#27a4ff 100%)}
.cover-art::after{content:"";position:absolute;right:30px;top:14px;width:190px;height:165px;border-radius:40%;background:radial-gradient(circle,rgba(10,30,120,.35),rgba(10,30,120,0) 70%)}
.cover-wave{position:absolute;left:0;top:0;width:464px;height:261px}
.cover-title{position:absolute;left:28px;top:54px;color:#fff;font-weight:700;font-size:22px;line-height:1.28}
.cover-name{position:absolute;left:28px;top:122px;color:#fff;font-size:11px;font-weight:500}
.cover-date{position:absolute;left:28px;top:140px;color:#fff;font-size:7px}
.cover-brand{position:absolute;left:0;right:0;top:222px;text-align:center;font-size:15px;font-weight:700;color:var(--blue)}
.dark .cover-brand{color:#ffffff}

/* title slide */
.deco{position:absolute;border-radius:50%;filter:blur(2px)}
.title-deco{left:220px;top:34px;width:230px;height:195px;background:radial-gradient(ellipse at 45% 50%,rgba(16,60,230,.85),rgba(30,140,255,.35) 55%,rgba(30,140,255,0) 72%)}
.wordmark{position:absolute;font-weight:700;color:var(--fg);line-height:1}
.title-mark{left:16px;top:70px}
.title-mark .big{display:block;font-size:42px;letter-spacing:1px}
.title-mark .small{display:block;font-size:17px;margin-top:4px}
.name-badge{position:absolute;left:16px;top:152px;width:156px;height:17px;background:linear-gradient(90deg,var(--blue),var(--sky));color:#fff;font-size:9.5px;font-weight:700;letter-spacing:3.2px;line-height:17px;padding-left:8px}
.title-date{position:absolute;left:16px;top:181px;font-size:8px;font-weight:700}

/* header + footer */
.head{position:absolute;left:0;top:0;width:464px;height:28px;background:var(--blue)}
.head::after{content:"";position:absolute;right:0;top:0;width:86px;height:28px;background:var(--sky);clip-path:polygon(16px 0,100% 0,100% 100%,0 100%)}
.head-strip{position:absolute;left:0;top:28px;width:245px;height:4px;background:var(--sky);clip-path:polygon(0 0,100% 0,98% 100%,0 100%)}
.head h2{position:absolute;left:29px;top:6px;color:#fff;font-size:13.5px;font-weight:700}
.foot{position:absolute;left:0;bottom:0;width:385px;height:10px;background:linear-gradient(90deg,var(--blue),var(--sky));clip-path:polygon(0 0,97% 0,100% 100%,0 100%);color:#fff;font-size:4.3px;line-height:10px}
.foot .page{position:absolute;left:28px;font-weight:700}
.foot .copy{position:absolute;left:182px}
.foot-brand{position:absolute;right:10px;bottom:4px;font-size:6.5px;font-weight:700;color:var(--blue)}
.dark .foot-brand{color:#fff}

/* bullets */
.bullets{position:absolute;list-style:none;width:200px}
.bullets li{position:relative;padding-left:11px;font-size:5.4px;line-height:9px;color:var(--muted);margin-bottom:6px}
.bullets li::before{content:"";position:absolute;left:0;top:2px;width:5px;height:5px;border-radius:50%;background:var(--blue);box-shadow:inset 0 0 0 1.2px var(--blue),inset 0 0 0 2px #fff}
.dark .bullets li::before{box-shadow:inset 0 0 0 1.2px var(--blue),inset 0 0 0 2px var(--navy)}
.bullets li.sub{margin-left:12px;margin-bottom:1px;line-height:9px}
.bullets li.sub::before{background:var(--sky)}
.bullets li.sub.last{margin-bottom:6px}
.b-left{left:28px;top:52px}
.b-right{left:245px;top:52px}
.b-chart{left:307px;top:60px;width:135px}
.b-chart li{margin-bottom:5px}

/* paragraphs */
.prose{position:absolute;top:68px;width:192px;font-size:5.3px;line-height:10.7px;color:var(--muted)}
.prose p{margin-bottom:6px}
.prose p.just{text-align:justify}
.p-left{left:28px}.p-right{left:245px}

/* chart */
.chart{position:absolute;left:12px;top:38px;width:285px;height:180px}
.chart text{font-family:'Roboto',Arial,sans-serif;fill:var(--muted)}

/* divider */
.divider-deco{left:0;top:10px;width:250px;height:230px;background:radial-gradient(ellipse at 45% 50%,rgba(60,110,240,.13),rgba(60,110,240,0) 70%)}
.dark .divider-deco{background:radial-gradient(ellipse at 45% 50%,rgba(40,70,200,.22),rgba(40,70,200,0) 70%)}
.div-num{position:absolute;left:286px;top:74px;font-size:32px;font-weight:700;color:var(--blue)}
.div-rule{position:absolute;left:287px;top:114px;width:38px;height:2px;background:var(--blue)}
.div-title{position:absolute;left:286px;top:134px;font-size:17px;font-weight:700;color:var(--fg)}
.div-sub{position:absolute;left:287px;top:170px;font-size:7.5px;font-weight:500;color:var(--fg)}

/* closing */
.close-deco{left:48px;top:62px;width:160px;height:140px;background:radial-gradient(ellipse,rgba(20,90,255,.9),rgba(20,120,255,.35) 55%,rgba(20,120,255,0) 72%)}
.close-mark{left:204px;top:92px;color:#fff}
.close-mark .big{display:block;font-size:48px;letter-spacing:1px}
.close-mark .small{display:block;font-size:19px;margin-top:3px;padding-left:2px}
.slide.closing{background:var(--navy)}
</style>
</head>
<body>

<!-- Cover slides -->
<section class="slide cover col-l r1">
  <div class="cover-art" role="img" aria-label="Blue circuit board photograph with glowing connection nodes"></div>
  <svg class="cover-wave" viewBox="0 0 464 261" aria-hidden="true">
    <path d="M0 222 Q232 172 464 222 V261 H0Z" fill="#ffffff"/>
    <path d="M0 222 Q232 172 464 222" fill="none" stroke="#0a22f0" stroke-width="4"/>
    <g fill="#fff" stroke="#0a22f0" stroke-width="1.2">
      <circle cx="14" cy="219" r="4.5"/><circle cx="55" cy="211" r="4.5"/><circle cx="93" cy="204" r="4.5"/>
      <circle cx="133" cy="199" r="4.5"/><circle cx="172" cy="196" r="4.5"/><circle cx="220" cy="195" r="4.5"/>
      <circle cx="270" cy="196" r="4.5"/><circle cx="316" cy="199" r="4.5"/><circle cx="360" cy="205" r="4.5"/>
      <circle cx="407" cy="212" r="4.5"/><circle cx="448" cy="219" r="4.5"/>
    </g>
  </svg>
  <h1 class="cover-title">TALON MICRO-<br>-SYSTEMS</h1>
  <p class="cover-name">Nora Castell</p>
  <p class="cover-date">December 2023</p>
  <p class="cover-brand">Talon Microsystems</p>
</section>

<section class="slide cover dark col-r r1">
  <div class="cover-art" role="img" aria-label="Blue circuit board photograph with glowing connection nodes"></div>
  <svg class="cover-wave" viewBox="0 0 464 261" aria-hidden="true">
    <path d="M0 222 Q232 172 464 222 V261 H0Z" fill="#02051f"/>
    <path d="M0 222 Q232 172 464 222" fill="none" stroke="#0a22f0" stroke-width="4"/>
    <g fill="#fff" stroke="#0a22f0" stroke-width="1.2">
      <circle cx="14" cy="219" r="4.5"/><circle cx="55" cy="211" r="4.5"/><circle cx="93" cy="204" r="4.5"/>
      <circle cx="133" cy="199" r="4.5"/><circle cx="172" cy="196" r="4.5"/><circle cx="220" cy="195" r="4.5"/>
      <circle cx="270" cy="196" r="4.5"/><circle cx="316" cy="199" r="4.5"/><circle cx="360" cy="205" r="4.5"/>
      <circle cx="407" cy="212" r="4.5"/><circle cx="448" cy="219" r="4.5"/>
    </g>
  </svg>
  <h1 class="cover-title">TALON MICRO-<br>-SYSTEMS</h1>
  <p class="cover-name">Nora Castell</p>
  <p class="cover-date">December 2023</p>
  <p class="cover-brand">Talon Microsystems</p>
</section>

<!-- Title slides -->
<section class="slide col-l r2">
  <div class="deco title-deco" role="img" aria-label="Large blue circuit-node decoration"></div>
  <p class="wordmark title-mark"><span class="big">TALON</span><span class="small">Microsystems</span></p>
  <p class="name-badge">NORA CASTELL</p>
  <p class="title-date">December, 2023</p>
</section>

<section class="slide dark col-r r2">
  <div class="deco title-deco" role="img" aria-label="Large blue circuit-node decoration"></div>
  <p class="wordmark title-mark"><span class="big">TALON</span><span class="small">Microsystems</span></p>
  <p class="name-badge">NORA CASTELL</p>
  <p class="title-date">December, 2023</p>
</section>

<!-- Title and bullet content -->
<section class="slide col-l r3">
  <header class="head"><h2>YOUR TITLE HERE</h2></header><div class="head-strip"></div>
  <ul class="bullets b-left">
    <li>Lorem ipsum dolor sit consectetur adipiscing sed do eiusmod tempor incididunt ut labore et dolore magna aliqua.</li>
    <li style="margin-bottom:1px">Lorem ipsum dolor sit consectetur adipiscing sed do eiusmod tempor incididunt ut labore et dolore magna aliqua.</li>
    <li class="sub">Duis aute irure dolor in reprehenderit in voluptate velit esse cillum</li>
    <li class="sub last">Duis aute irure dolor in reprehenderit in voluptate velit esse cillum</li>
    <li>Lorem ipsum dolor sit consectetur adipiscing sed do eiusmod tempor incididunt ut labore et dolore magna aliqua.</li>
    <li>Lorem ipsum dolor sit consectetur adipiscing sed do eiusmod tempor incididunt ut labore et dolore magna aliqua.</li>
    <li>Lorem ipsum dolor sit consectetur adipiscing sed do eiusmod tempor incididunt ut labore et dolore magna aliqua.</li>
    <li>Lorem ipsum dolor sit consectetur adipiscing sed do eiusmod tempor incididunt ut labore et dolore magna aliqua.</li>
    <li>Lorem ipsum dolor sit consectetur adipiscing sed do eiusmod tempor incididunt ut labore et dolore magna aliqua.</li>
  </ul>
  <ul class="bullets b-right">
    <li>Lorem ipsum dolor sit consectetur adipiscing sed do eiusmod tempor incididunt ut labore et dolore magna aliqua.</li>
    <li>Lorem ipsum dolor sit consectetur adipiscing sed do eiusmod tempor incididunt ut labore et dolore magna aliqua.</li>
    <li>Lorem ipsum dolor sit consectetur adipiscing sed do eiusmod tempor incididunt ut labore et dolore magna aliqua.</li>
    <li>Lorem ipsum dolor sit consectetur adipiscing sed do eiusmod tempor incididunt ut labore et dolore magna aliqua.</li>
    <li>Lorem ipsum dolor sit consectetur adipiscing sed do eiusmod tempor incididunt ut labore et dolore magna aliqua.</li>
    <li>Lorem ipsum dolor sit consectetur adipiscing sed do eiusmod tempor incididunt ut labore et dolore magna aliqua.</li>
    <li>Lorem ipsum dolor sit consectetur adipiscing sed do eiusmod tempor incididunt ut labore et dolore magna aliqua.</li>
    <li>Lorem ipsum dolor sit consectetur adipiscing sed do eiusmod tempor incididunt ut labore et dolore magna aliqua.</li>
  </ul>
  <footer><div class="foot"><span class="page">PAGE | 02</span><span class="copy">© 2023 Company Name | All Rights Reserved</span></div><span class="foot-brand">Talon Microsystems</span></footer>
</section>

<section class="slide dark col-r r3">
  <header class="head"><h2>YOUR TITLE HERE</h2></header><div class="head-strip"></div>
  <ul class="bullets b-left">
    <li>Lorem ipsum dolor sit consectetur adipiscing sed do eiusmod tempor incididunt ut labore et dolore magna aliqua.</li>
    <li style="margin-bottom:1px">Lorem ipsum dolor sit consectetur adipiscing sed do eiusmod tempor incididunt ut labore et dolore magna aliqua.</li>
    <li class="sub">Duis aute irure dolor in reprehenderit in voluptate velit esse cillum</li>
    <li class="sub last">Duis aute irure dolor in reprehenderit in voluptate velit esse cillum</li>
    <li>Lorem ipsum dolor sit consectetur adipiscing sed do eiusmod tempor incididunt ut labore et dolore magna aliqua.</li>
    <li>Lorem ipsum dolor sit consectetur adipiscing sed do eiusmod tempor incididunt ut labore et dolore magna aliqua.</li>
    <li>Lorem ipsum dolor sit consectetur adipiscing sed do eiusmod tempor incididunt ut labore et dolore magna aliqua.</li>
    <li>Lorem ipsum dolor sit consectetur adipiscing sed do eiusmod tempor incididunt ut labore et dolore magna aliqua.</li>
    <li>Lorem ipsum dolor sit consectetur adipiscing sed do eiusmod tempor incididunt ut labore et dolore magna aliqua.</li>
  </ul>
  <ul class="bullets b-right">
    <li>Lorem ipsum dolor sit consectetur adipiscing sed do eiusmod tempor incididunt ut labore et dolore magna aliqua.</li>
    <li>Lorem ipsum dolor sit consectetur adipiscing sed do eiusmod tempor incididunt ut labore et dolore magna aliqua.</li>
    <li>Lorem ipsum dolor sit consectetur adipiscing sed do eiusmod tempor incididunt ut labore et dolore magna aliqua.</li>
    <li>Lorem ipsum dolor sit consectetur adipiscing sed do eiusmod tempor incididunt ut labore et dolore magna aliqua.</li>
    <li>Lorem ipsum dolor sit consectetur adipiscing sed do eiusmod tempor incididunt ut labore et dolore magna aliqua.</li>
    <li>Lorem ipsum dolor sit consectetur adipiscing sed do eiusmod tempor incididunt ut labore et dolore magna aliqua.</li>
    <li>Lorem ipsum dolor sit consectetur adipiscing sed do eiusmod tempor incididunt ut labore et dolore magna aliqua.</li>
    <li>Lorem ipsum dolor sit consectetur adipiscing sed do eiusmod tempor incididunt ut labore et dolore magna aliqua.</li>
  </ul>
  <footer><div class="foot"><span class="page">PAGE | 02</span><span class="copy">© 2023 Company Name | All Rights Reserved</span></div><span class="foot-brand">Talon Microsystems</span></footer>
</section>

<!-- Two column text -->
<section class="slide col-l r4">
  <header class="head"><h2>YOUR TITLE HERE</h2></header><div class="head-strip"></div>
  <div class="prose p-left">
    <p>Lorem ipsum dolor sit amet, consectetur adipiscing elit, sed do eiusmod tempor incididunt ut labore et dolore magna aliqua. Ut enim ad minim veniam, quis nostrud exercitation ullamco laboris nisi ut aliquip ex ea commodo consequat. Duis aute irure dolor in reprehenderit in voluptate velit esse cillum dolore eu fugiat nulla pariatur. Excepteur sint occaecat cupidatat non proident, sunt in culpa qui officia deserunt mollit anim id est laborum.</p>
    <p class="just">Sed ut perspiciatis unde omnis iste natus error sit voluptatem accusantium doloremque laudantium, totam rem aperiam, eaque ipsa quae ab illo inventore veritatis et quasi architecto beatae vitae dicta sunt explicabo. Nemo enim ipsam voluptatem quia voluptas sit aspernatur aut odit aut fugit, sed quia consequuntur magni dolores eos qui ratione voluptatem sequi nesciunt. Neque porro quisquam est, qui dolorem ipsum quia dolor sit amet, consectetur, adipisci velit, sed quia non numquam eius modi tempora incidunt ut labore et dolore magnam aliquam quaerat voluptatem.</p>
  </div>
  <div class="prose p-right">
    <p>Lorem ipsum dolor sit amet, consectetur adipiscing elit, sed do eiusmod tempor incididunt ut labore et dolore magna aliqua. Ut enim ad minim veniam, quis nostrud exercitation ullamco laboris nisi ut aliquip ex ea commodo consequat. Duis aute irure dolor in reprehenderit in voluptate velit esse cillum dolore eu fugiat nulla pariatur. Excepteur sint occaecat cupidatat non proident, sunt in culpa qui officia deserunt mollit anim id est laborum.</p>
    <p class="just">Sed ut perspiciatis unde omnis iste natus error sit voluptatem accusantium doloremque laudantium, totam rem aperiam, eaque ipsa quae ab illo inventore veritatis et quasi architecto beatae vitae dicta sunt explicabo. Nemo enim ipsam voluptatem quia voluptas sit aspernatur aut odit aut fugit, sed quia consequuntur magni dolores eos qui ratione voluptatem sequi nesciunt. Neque porro quisquam est, qui dolorem ipsum quia dolor sit amet, consectetur, adipisci velit, sed quia non numquam eius modi tempora incidunt ut labore et dolore magnam aliquam quaerat voluptatem.</p>
  </div>
  <footer><div class="foot"><span class="page">PAGE | 03</span><span class="copy">© 2023 Company Name | All Rights Reserved</span></div><span class="foot-brand">Talon Microsystems</span></footer>
</section>

<section class="slide dark col-r r4">
  <header class="head"><h2>YOUR TITLE HERE</h2></header><div class="head-strip"></div>
  <div class="prose p-left">
    <p>Lorem ipsum dolor sit amet, consectetur adipiscing elit, sed do eiusmod tempor incididunt ut labore et dolore magna aliqua. Ut enim ad minim veniam, quis nostrud exercitation ullamco laboris nisi ut aliquip ex ea commodo consequat. Duis aute irure dolor in reprehenderit in voluptate velit esse cillum dolore eu fugiat nulla pariatur. Excepteur sint occaecat cupidatat non proident, sunt in culpa qui officia deserunt mollit anim id est laborum.</p>
    <p class="just">Sed ut perspiciatis unde omnis iste natus error sit voluptatem accusantium doloremque laudantium, totam rem aperiam, eaque ipsa quae ab illo inventore veritatis et quasi architecto beatae vitae dicta sunt explicabo. Nemo enim ipsam voluptatem quia voluptas sit aspernatur aut odit aut fugit, sed quia consequuntur magni dolores eos qui ratione voluptatem sequi nesciunt. Neque porro quisquam est, qui dolorem ipsum quia dolor sit amet, consectetur, adipisci velit, sed quia non numquam eius modi tempora incidunt ut labore et dolore magnam aliquam quaerat voluptatem.</p>
  </div>
  <div class="prose p-right">
    <p>Lorem ipsum dolor sit amet, consectetur adipiscing elit, sed do eiusmod tempor incididunt ut labore et dolore magna aliqua. Ut enim ad minim veniam, quis nostrud exercitation ullamco laboris nisi ut aliquip ex ea commodo consequat. Duis aute irure dolor in reprehenderit in voluptate velit esse cillum dolore eu fugiat nulla pariatur. Excepteur sint occaecat cupidatat non proident, sunt in culpa qui officia deserunt mollit anim id est laborum.</p>
    <p class="just">Sed ut perspiciatis unde omnis iste natus error sit voluptatem accusantium doloremque laudantium, totam rem aperiam, eaque ipsa quae ab illo inventore veritatis et quasi architecto beatae vitae dicta sunt explicabo. Nemo enim ipsam voluptatem quia voluptas sit aspernatur aut odit aut fugit, sed quia consequuntur magni dolores eos qui ratione voluptatem sequi nesciunt. Neque porro quisquam est, qui dolorem ipsum quia dolor sit amet, consectetur, adipisci velit, sed quia non numquam eius modi tempora incidunt ut labore et dolore magnam aliquam quaerat voluptatem.</p>
  </div>
  <footer><div class="foot"><span class="page">PAGE | 03</span><span class="copy">© 2023 Company Name | All Rights Reserved</span></div><span class="foot-brand">Talon Microsystems</span></footer>
</section>

<!-- Chart slides -->
<section class="slide col-l r5">
  <header class="head"><h2>YOUR TITLE HERE</h2></header><div class="head-strip"></div>
  <svg class="chart" viewBox="0 0 285 180" aria-label="Bar chart by weekday">
    <rect x="30" y="10" width="245" height="150" fill="var(--plot)" stroke="var(--grid)" stroke-width=".6"/>
    <g stroke="var(--grid)" stroke-width=".6"><line x1="65" y1="10" x2="65" y2="160"/><line x1="100" y1="10" x2="100" y2="160"/><line x1="135" y1="10" x2="135" y2="160"/><line x1="170" y1="10" x2="170" y2="160"/><line x1="205" y1="10" x2="205" y2="160"/><line x1="240" y1="10" x2="240" y2="160"/></g>
    <g font-size="5" text-anchor="end"><text x="22" y="12">120</text><text x="22" y="37">100</text><text x="22" y="62">80</text><text x="22" y="87">60</text><text x="22" y="112">40</text><text x="22" y="137">20</text><text x="22" y="162">0</text></g>
    <g fill="#0a22f0"><rect x="38" y="35" width="7" height="125"/><rect x="73" y="47.5" width="7" height="112.5"/><rect x="108" y="97.5" width="7" height="62.5"/><rect x="143" y="35" width="7" height="125"/><rect x="178" y="35" width="7" height="125"/><rect x="213" y="85" width="7" height="75"/><rect x="248" y="97.5" width="7" height="62.5"/></g>
    <g fill="#1eaaff"><rect x="49" y="47.5" width="7" height="112.5"/><rect x="84" y="60" width="7" height="100"/><rect x="119" y="35" width="7" height="125"/><rect x="154" y="85" width="7" height="75"/><rect x="189" y="47.5" width="7" height="112.5"/><rect x="224" y="66.25" width="7" height="93.75"/><rect x="259" y="35" width="7" height="125"/></g>
    <g font-size="4.6" text-anchor="middle" font-weight="700"><text x="41.5" y="32">100</text><text x="52.5" y="44.5">90</text><text x="76.5" y="44.5">90</text><text x="87.5" y="57">80</text><text x="111.5" y="94.5">50</text><text x="122.5" y="32">100</text><text x="146.5" y="32">100</text><text x="157.5" y="82">60</text><text x="181.5" y="32">100</text><text x="192.5" y="44.5">90</text><text x="216.5" y="82">60</text><text x="227.5" y="63">75</text><text x="251.5" y="94.5">50</text><text x="262.5" y="32">100</text></g>
    <g font-size="5.5" text-anchor="middle" font-weight="700"><text x="47" y="170">Sun</text><text x="82" y="170">Mon</text><text x="117" y="170">Tue</text><text x="152" y="170">Wed</text><text x="187" y="170">Thu</text><text x="222" y="170">Fri</text><text x="257" y="170">Sat</text></g>
  </svg>
  <ul class="bullets b-chart">
    <li>Lorem ipsum dolor sit consectetur adipiscing elit, sed do eiusmod tempor incididunt ut labore et dolore magna aliqua.</li>
    <li>Lorem ipsum dolor sit consectetur adipiscing elit, sed do eiusmod</li>
    <li>Lorem ipsum dolor sit consectetur adipiscing elit, sed do eiusmod tempor incididunt ut labore et dolore magna aliqua.</li>
    <li>Lorem ipsum dolor sit consectetur adipiscing elit, sed do eiusmod</li>
    <li>Lorem ipsum dolor sit consectetur adipiscing elit, sed do eiusmod tempor incididunt ut labore et dolore magna aliqua.</li>
    <li>Lorem ipsum dolor sit consectetur adipiscing elit, sed do eiusmod</li>
  </ul>
  <footer><div class="foot"><span class="page">PAGE | 04</span><span class="copy">© 2023 Company Name | All Rights Reserved</span></div><span class="foot-brand">Talon Microsystems</span></footer>
</section>

<section class="slide dark col-r r5">
  <header class="head"><h2>YOUR TITLE HERE</h2></header><div class="head-strip"></div>
  <svg class="chart" viewBox="0 0 285 180" aria-label="Bar chart by weekday">
    <rect x="30" y="10" width="245" height="150" fill="var(--plot)" stroke="var(--grid)" stroke-width=".6"/>
    <g stroke="var(--grid)" stroke-width=".6"><line x1="65" y1="10" x2="65" y2="160"/><line x1="100" y1="10" x2="100" y2="160"/><line x1="135" y1="10" x2="135" y2="160"/><line x1="170" y1="10" x2="170" y2="160"/><line x1="205" y1="10" x2="205" y2="160"/><line x1="240" y1="10" x2="240" y2="160"/></g>
    <g font-size="5" text-anchor="end" opacity=".45"><text x="22" y="12">120</text><text x="22" y="37">100</text><text x="22" y="62">80</text><text x="22" y="87">60</text><text x="22" y="112">40</text><text x="22" y="137">20</text><text x="22" y="162">0</text></g>
    <g fill="#0a22f0"><rect x="38" y="35" width="7" height="125"/><rect x="73" y="47.5" width="7" height="112.5"/><rect x="108" y="97.5" width="7" height="62.5"/><rect x="143" y="35" width="7" height="125"/><rect x="178" y="35" width="7" height="125"/><rect x="213" y="85" width="7" height="75"/><rect x="248" y="97.5" width="7" height="62.5"/></g>
    <g fill="#1eaaff"><rect x="49" y="47.5" width="7" height="112.5"/><rect x="84" y="60" width="7" height="100"/><rect x="119" y="35" width="7" height="125"/><rect x="154" y="85" width="7" height="75"/><rect x="189" y="47.5" width="7" height="112.5"/><rect x="224" y="66.25" width="7" height="93.75"/><rect x="259" y="35" width="7" height="125"/></g>
    <g font-size="4.6" text-anchor="middle" opacity=".45"><text x="41.5" y="32">100</text><text x="52.5" y="44.5">90</text><text x="76.5" y="44.5">90</text><text x="87.5" y="57">80</text><text x="111.5" y="94.5">50</text><text x="122.5" y="32">100</text><text x="146.5" y="32">100</text><text x="157.5" y="82">60</text><text x="181.5" y="32">100</text><text x="192.5" y="44.5">90</text><text x="216.5" y="82">60</text><text x="227.5" y="63">75</text><text x="251.5" y="94.5">50</text><text x="262.5" y="32">100</text></g>
    <g font-size="5.5" text-anchor="middle" opacity=".45"><text x="47" y="170">Sun</text><text x="82" y="170">Mon</text><text x="117" y="170">Tue</text><text x="152" y="170">Wed</text><text x="187" y="170">Thu</text><text x="222" y="170">Fri</text><text x="257" y="170">Sat</text></g>
  </svg>
  <ul class="bullets b-chart">
    <li>Lorem ipsum dolor sit consectetur adipiscing elit, sed do eiusmod tempor incididunt ut labore et dolore magna aliqua.</li>
    <li>Lorem ipsum dolor sit consectetur adipiscing elit, sed do eiusmod</li>
    <li>Lorem ipsum dolor sit consectetur adipiscing elit, sed do eiusmod tempor incididunt ut labore et dolore magna aliqua.</li>
    <li>Lorem ipsum dolor sit consectetur adipiscing elit, sed do eiusmod</li>
    <li>Lorem ipsum dolor sit consectetur adipiscing elit, sed do eiusmod tempor incididunt ut labore et dolore magna aliqua.</li>
    <li>Lorem ipsum dolor sit consectetur adipiscing elit, sed do eiusmod</li>
  </ul>
  <footer><div class="foot"><span class="page">PAGE | 04</span><span class="copy">© 2023 Company Name | All Rights Reserved</span></div><span class="foot-brand">Talon Microsystems</span></footer>
</section>

<!-- Divider slides -->
<section class="slide col-l r6">
  <div class="deco divider-deco" role="img" aria-label="Faint circuit-node decoration"></div>
  <p class="div-num">02</p><div class="div-rule"></div>
  <h2 class="div-title">DIVIDER SLIDE</h2>
  <p class="div-sub">Subtile Goes Here</p>
  <footer><div class="foot"><span class="page">PAGE | 05</span><span class="copy">© 2023 Company Name | All Rights Reserved</span></div><span class="foot-brand">Talon Microsystems</span></footer>
</section>

<section class="slide dark col-r r6">
  <div class="deco divider-deco" role="img" aria-label="Faint circuit-node decoration"></div>
  <p class="div-num">02</p><div class="div-rule"></div>
  <h2 class="div-title">DIVIDER SLIDE</h2>
  <p class="div-sub">Subtile Goes Here</p>
  <footer><div class="foot"><span class="page">PAGE | 05</span><span class="copy">© 2023 Company Name | All Rights Reserved</span></div><span class="foot-brand">Talon Microsystems</span></footer>
</section>

<!-- Closing slides -->
<section class="slide dark closing col-l r7">
  <div class="deco close-deco" role="img" aria-label="Blue circuit-node decoration"></div>
  <p class="wordmark close-mark"><span class="big">TALON</span><span class="small">Microsystems</span></p>
  <footer><div class="foot"><span class="page">PAGE | 06</span><span class="copy">© 2023 Company Name | All Rights Reserved</span></div><span class="foot-brand">Talon Microsystems</span></footer>
</section>

<section class="slide dark closing col-r r7">
  <div class="deco close-deco" role="img" aria-label="Blue circuit-node decoration"></div>
  <p class="wordmark close-mark"><span class="big">TALON</span><span class="small">Microsystems</span></p>
  <footer><div class="foot"><span class="page">PAGE | 06</span><span class="copy">© 2023 Company Name | All Rights Reserved</span></div><span class="foot-brand">Talon Microsystems</span></footer>
</section>

</body>
</html>
```